Business Card Design For A Cajun Seafood Restaurant

We are opening a cajun seafood restaurant in a week. We mainly serve cajun seafood which is orginally from Louisiana. We want design on both sides of a business card. I have menu on the website. You can go to www.reednkettle.example to check out our menu.

Restaurant name: Reedkettle House
Phone: +1 (555) 304-7712
Address: 48206 Ludlow Row, #7, Bexmoor Flats, Ca90000
Email: reednkettle@mailbox.example
Website: www.reednkettle.example

Maybe add social media icons (facebook, instagram) if looks nice on the business card.
social.example/reednkettle
photos.example/reednkettle or @reednkettle

Attached is the logo and other business card samples that I like.

```html
<!DOCTYPE html>
<html lang="en">
<head>
<meta charset="utf-8">
<title>Reedkettle House — Business Card</title>
<link href="https://fonts.googleapis.com/css2?family=Montserrat:wght@400;500;700;800&display=swap" rel="stylesheet">
<style>
  :root {
    --stage: #3a3a3a;
    --card-dark: #1c1c1c;
    --card-light: #ffffff;
    --accent: #f26522;
    --ink: #1e1e1e;
    --on-dark: #ffffff;
    --rule: #444444;
  }
  * { margin: 0; padding: 0; box-sizing: border-box; }
  html, body { width: 1200px; height: 900px; overflow: hidden; }
  body {
    background: var(--stage);
    font-family: "Montserrat", sans-serif;
    display: flex;
    flex-direction: column;
    align-items: center;
    justify-content: center;
    gap: 36px;
  }
  .card {
    width: 700px;
    height: 400px;
    border-radius: 26px;
    position: relative;
    box-shadow: 0 10px 30px rgba(0,0,0,.35);
  }
  .brand {
    display: flex;
    align-items: center;
    gap: 14px;
    font-weight: 800;
    font-size: 40px;
    letter-spacing: .5px;
    white-space: nowrap;
  }
  .brand__dot {
    width: 26px; height: 26px;
    border-radius: 50%;
    background: var(--accent);
    flex: none;
  }

  /* Front */
  .card--front {
    background: var(--card-dark);
    display: flex;
    flex-direction: column;
    align-items: center;
    justify-content: center;
    gap: 34px;
  }
  .card--front .brand { color: var(--on-dark); }
  .website {
    color: var(--on-dark);
    font-size: 20px;
    font-weight: 400;
    letter-spacing: .5px;
  }
  .website em { font-style: normal; color: var(--accent); font-weight: 700; }

  /* Back */
  .card--back {
    background: var(--card-light);
    display: grid;
    grid-template-columns: 340px 1px 1fr;
    align-items: center;
  }
  .card--back .brand {
    color: var(--ink);
    font-size: 26px;
    gap: 12px;
    justify-self: center;
  }
  .card--back .brand__dot { width: 18px; height: 18px; }
  .divider {
    width: 1px;
    height: 200px;
    background: var(--rule);
  }
  .contact { padding-left: 30px; color: var(--ink); }
  .contact__name {
    color: var(--accent);
    font-size: 26px;
    font-weight: 700;
    line-height: 1.1;
  }
  .contact__role { font-size: 15px; margin-bottom: 8px; }
  .contact__address { font-size: 15px; line-height: 1.4; margin-bottom: 4px; }
  .contact__list { list-style: none; font-size: 15px; line-height: 1.5; }
  .contact__list li { display: flex; align-items: center; gap: 10px; }
  .contact__icon { width: 13px; height: 13px; flex: none; display: flex; align-items: center; justify-content: center; }
  .contact__icon svg { width: 13px; height: 13px; }
  .contact__list em { font-style: normal; color: var(--accent); font-weight: 700; }
  .mark-plain { width: 10px; height: 10px; background: var(--accent); }
  .mark-plain--round { border-radius: 50%; }
</style>
</head>
<body>
  <section class="card card--front">
    <div class="brand"><span class="brand__dot"></span><span>Reedkettle House</span></div>
    <p class="website">www.<em>reednkettle</em>.example</p>
  </section>

  <section class="card card--back">
    <div class="brand"><span class="brand__dot"></span><span>Reedkettle House</span></div>
    <span class="divider"></span>
    <div class="contact">
      <h1 class="contact__name">Marlo Fenwick</h1>
      <p class="contact__role">Director</p>
      <p class="contact__address">48206 Ludlow Row<br>#7, Bexmoor Flats, Ca90000</p>
      <ul class="contact__list">
        <li>
          <span class="contact__icon"><svg viewBox="0 0 24 24" aria-hidden="true"><path fill="#f26522" d="M6.6 10.8a15 15 0 0 0 6.6 6.6l2.2-2.2a1 1 0 0 1 1-.25 11.4 11.4 0 0 0 3.6.57 1 1 0 0 1 1 1V20a1 1 0 0 1-1 1A17 17 0 0 1 3 4a1 1 0 0 1 1-1h3.5a1 1 0 0 1 1 1c0 1.25.2 2.45.57 3.57a1 1 0 0 1-.25 1z"/></svg></span>
          <span>+1 (555) 304-7712</span>
        </li>
        <li>
          <span class="contact__icon"><svg viewBox="0 0 24 24" aria-hidden="true"><rect x="2" y="5" width="20" height="14" rx="2" fill="none" stroke="#f26522" stroke-width="2.4"/><path d="M3 6l9 7 9-7" fill="none" stroke="#f26522" stroke-width="2.4"/></svg></span>
          <span>reednkettle@mailbox.example</span>
        </li>
        <li>
          <span class="contact__icon"><svg viewBox="0 0 24 24" aria-hidden="true"><circle cx="12" cy="12" r="9.5" fill="none" stroke="#f26522" stroke-width="2.2"/><ellipse cx="12" cy="12" rx="4" ry="9.5" fill="none" stroke="#f26522" stroke-width="2"/><path d="M3 12h18" stroke="#f26522" stroke-width="2"/></svg></span>
          <span>www.<em>reednkettle</em>.example</span>
        </li>
        <li><span class="contact__icon"><span class="mark-plain mark-plain--round"></span></span><span>social.example/reednkettle</span></li>
        <li><span class="contact__icon"><span class="mark-plain"></span></span><span>photos.example/reednkettle</span></li>
      </ul>
    </div>
  </section>
</body>
</html>
```